Tall Fern Roofing Business Card

Need a business card with the logo that was designed here

Contact Information for Business Card

Name, Title, Phone, Email, Website, Company name

```html
<!DOCTYPE html>
<html lang="en">
<head>
<meta charset="utf-8">
<title>Tall Fern Roofing Business Card</title>
<link href="https://fonts.googleapis.com/css2?family=Open+Sans:wght@400;600;700;800&display=swap" rel="stylesheet">
<style>
  :root {
    --stage: #242424;
    --card: #212226;
    --blue: #1a7bd0;
    --blue-deep: #0e6fbc;
    --grey: #9a9ca1;
    --white: #ffffff;
    --pattern-dark: #1b1c20;
    --pattern-light: #3a3b40;
  }
  * { box-sizing: border-box; margin: 0; padding: 0; }
  html, body {
    width: 1200px; height: 780px; overflow: hidden;
    background: var(--stage);
    font-family: "Open Sans", Arial, sans-serif;
  }
  .canvas {
    position: relative; width: 1200px; height: 780px;
    display: flex; align-items: center; justify-content: center; gap: 40px;
  }
  .card {
    position: relative; width: 560px; height: 320px;
    border-radius: 18px; overflow: hidden;
    background: var(--card);
    box-shadow: 0 0 0 3px var(--blue), 0 18px 40px rgba(0,0,0,.55);
  }
  /* back */
  .back-pattern {
    position: absolute; inset: 0;
    background: linear-gradient(200deg, var(--pattern-light) 0%, var(--pattern-dark) 45%, var(--card) 100%);
  }
  .back-name {
    position: absolute; right: 40px; bottom: 70px;
    font-weight: 700; font-size: 24px; color: var(--blue);
    display: flex; align-items: center; gap: 10px;
  }
  .mark-square { width: 14px; height: 14px; background: var(--blue); }
  /* front */
  .front-name {
    position: absolute; left: 34px; top: 128px; width: 220px;
    font-weight: 700; font-size: 26px; line-height: 1.15; color: var(--blue);
  }
  .divider {
    position: absolute; left: 268px; top: 52px; width: 2px; height: 170px;
    background: var(--white);
  }
  .details { position: absolute; left: 292px; top: 44px; color: var(--white); }
  .person { font-size: 32px; font-weight: 800; line-height: 1.1; }
  .person .first { color: var(--blue); }
  .person .last { color: var(--grey); }
  .title { font-size: 14px; font-weight: 600; margin-top: 4px; }
  .address { font-size: 13px; line-height: 1.35; margin-top: 14px; }
  .contacts { list-style: none; margin-top: 14px; font-size: 13px; line-height: 1.5; }
  .contacts li { display: flex; align-items: center; gap: 8px; }
  .contacts svg { width: 13px; height: 13px; fill: var(--blue); flex: none; }
  .bands { position: absolute; left: 0; bottom: 0; width: 560px; height: 80px; }
</style>
</head>
<body>
<main class="canvas">

  <section class="card card-back">
    <div class="back-pattern" role="img" aria-label="Repeating pattern of small house roof outlines in dark and silver tones"></div>
    <div class="back-name"><span class="mark-square"></span>Tall Fern Roofing</div>
  </section>

  <section class="card card-front">
    <div class="front-name">Tall Fern Roofing</div>
    <div class="divider"></div>
    <div class="details">
      <h1 class="person"><span class="first">Mark</span> <span class="last">Dalton</span></h1>
      <p class="title">Managing Director</p>
      <p class="address">1840 Willow Bend Rd. Suite<br>310 Arlington, TX 76010</p>
      <ul class="contacts">
        <li><svg viewBox="0 0 24 24"><path d="M6.6 10.8a15.1 15.1 0 0 0 6.6 6.6l2.2-2.2a1 1 0 0 1 1-.25 11.4 11.4 0 0 0 3.6.57 1 1 0 0 1 1 1V20a1 1 0 0 1-1 1A17 17 0 0 1 3 4a1 1 0 0 1 1-1h3.5a1 1 0 0 1 1 1c0 1.25.2 2.45.57 3.57a1 1 0 0 1-.25 1z"/></svg>(555) 214-6083</li>
        <li><svg viewBox="0 0 24 24"><path d="M2 5h20v14H2zm2 2v.5l8 5 8-5V7l-8 5z"/></svg>info@website.com</li>
        <li><svg viewBox="0 0 24 24"><circle cx="12" cy="12" r="10"/></svg>www.website.com</li>
      </ul>
    </div>
    <svg class="bands" viewBox="0 0 560 80" aria-hidden="true">
      <polygon points="290,34 560,14 560,36 310,52" fill="var(--grey)"/>
      <polygon points="0,64 300,44 330,46 0,74" fill="var(--blue-deep)"/>
      <polygon points="0,78 560,46 560,80 0,80" fill="var(--blue)"/>
    </svg>
  </section>

</main>
</body>
</html>
```